Local Flower Farm Needs Business Card Design

I need business cards designed for a flower farm based in Eudora, Kansas.
Business Info:
We are a local cut flower farm located in Eudora, Kansas, founded by Corinne Haldwick. What started as a passion for agriculture and search for more joy in daily life has blossomed into a small business dedicated to providing the community with beautiful, fresh, and sustainable flowers. We specialize in local, seasonal blooms, ensuring that every petal reflects the care and dedication we pour into our craft. Our mission is to deliver the highest quality flowers directly to our customers through local farmers markets and to florists who share our commitment to sustainability. Join us in celebrating the beauty of nature, one bloom at a time!
Contact Details:
Corinne Haldwick
Owner
Phone 913-555-0147
Facebook: Rosalind Thorpe Gardens
Instagram: @RosalindThorpeGardens
Website: RosalindThorpeGardens.example
Target Market(s)
Wholesale to Florists and Direct to Consumer via Farmers Market
Industry/Entity Type
Florist, Farm
Contact Information for Business Card
Name, Contact Info, Logo
Look and feel
Each slider illustrates characteristics of the customer's brand and the style your logo design should communicate.

```html
<!DOCTYPE html>
<html lang="en">
<head>
<meta charset="utf-8">
<title>Rosalind Thorpe Gardens – Business Card</title>
<link href="https://fonts.googleapis.com/css2?family=EB+Garamond:wght@400;700&display=swap" rel="stylesheet">
<style>
  :root {
    --backdrop: #1b1d1f;
    --teal-deep: #071a1d;
    --teal: #0d2c30;
    --teal-faint: #1d4447;
    --paper: #ffffff;
    --ink: #0b2529;
    --ink-soft: #4d5557;
  }
  html, body {
    margin: 0;
    width: 1200px;
    height: 840px;
    overflow: hidden;
    background: var(--backdrop);
    font-family: "EB Garamond", Georgia, serif;
  }
  .stage {
    position: relative;
    width: 1200px;
    height: 840px;
  }
  .card {
    position: absolute;
    top: 266px;
    width: 540px;
    height: 308px;
    border-radius: 24px;
    overflow: hidden;
    box-shadow: 0 10px 30px rgba(0,0,0,.45);
  }
  .card--back {
    left: 36px;
    background: linear-gradient(135deg, var(--teal) 0%, var(--teal-deep) 70%);
  }
  .card--front { left: 624px; background: var(--teal-deep); }
  .card-art { position: absolute; inset: 0; }

  .brand-seal {
    position: absolute;
    display: flex;
    align-items: center;
    justify-content: center;
    text-align: center;
    border-radius: 50%;
    font-weight: 400;
    letter-spacing: .12em;
    text-transform: uppercase;
    line-height: 1.35;
  }
  .card--back .brand-seal {
    left: 40px; top: 44px; width: 216px; height: 216px;
    border: 1.5px solid var(--paper);
    color: var(--paper);
    font-size: 21px;
  }
  .card--front .brand-seal {
    left: 116px; top: 76px; width: 176px; height: 176px;
    border: 1.5px solid var(--ink);
    color: var(--ink);
    font-size: 17px;
  }

  .contact {
    position: absolute;
    left: 296px;
    top: 34px;
    width: 236px;
    color: var(--ink);
  }
  .contact__name {
    margin: 0;
    font-size: 21px;
    line-height: 26px;
    font-weight: 700;
    letter-spacing: .02em;
    text-transform: uppercase;
    white-space: nowrap;
  }
  .contact__role {
    margin: 0 0 14px;
    font-size: 16px;
    line-height: 20px;
    color: var(--ink-soft);
  }
  .contact__list { list-style: none; margin: 0; padding: 0; }
  .contact__item {
    display: flex;
    align-items: center;
    gap: 7px;
    font-size: 14.5px;
    line-height: 21px;
    color: var(--ink-soft);
    white-space: nowrap;
  }
  .contact__icon { width: 13px; height: 13px; flex: none; display: block; }
</style>
</head>
<body>
<main class="stage">

  <section class="card card--back" aria-label="Card back">
    <svg class="card-art" width="540" height="308" viewBox="0 0 540 308" aria-hidden="true">
      <circle cx="440" cy="120" r="150" fill="var(--teal-faint)" opacity=".45"/>
    </svg>
    <div class="brand-seal">Rosalind<br>Thorpe<br>Gardens</div>
  </section>

  <section class="card card--front" aria-label="Card front">
    <svg class="card-art" width="540" height="308" viewBox="0 0 540 308" aria-hidden="true">
      <path fill="var(--paper)"
            d="M110,0 H540 V196 C470,202 420,240 360,268 C300,296 240,304 198,298 C118,288 78,228 78,158 C78,84 96,32 110,0 Z"/>
      <path fill="none" stroke="var(--paper)" stroke-width="1.2"
            d="M52,100 C44,170 62,236 108,268 M126,278 C200,300 270,290 330,264 M350,254 C400,230 440,212 470,202 M484,196 C505,190 520,188 532,187"/>
      <g fill="var(--paper)">
        <circle cx="52" cy="100" r="2.5"/><circle cx="108" cy="268" r="2.5"/>
        <circle cx="126" cy="278" r="2.5"/><circle cx="330" cy="264" r="2.5"/>
        <circle cx="350" cy="254" r="2.5"/><circle cx="470" cy="202" r="2.5"/>
        <circle cx="484" cy="196" r="2.5"/>
      </g>
    </svg>

    <div class="brand-seal">Rosalind<br>Thorpe<br>Gardens</div>

    <div class="contact">
      <h1 class="contact__name">Corinne Haldwick</h1>
      <p class="contact__role">Owner</p>
      <ul class="contact__list">
        <li class="contact__item">
          <svg class="contact__icon" viewBox="0 0 16 16" aria-label="Phone"><path fill="var(--ink)" d="M3.6 1.5l2.3 2.6-1.3 1.8c.9 2 2.4 3.6 4.5 4.6l1.8-1.3 2.6 2.3-1.4 2.2C7 13.4 2.6 9 1.4 2.9z"/></svg>
          913-555-0147
        </li>
        <li class="contact__item">
          <svg class="contact__icon" viewBox="0 0 16 16" aria-hidden="true"><rect x="1" y="1" width="14" height="14" rx="3" fill="var(--ink)"/></svg>
          Rosalind Thorpe Gardens
        </li>
        <li class="contact__item">
          <svg class="contact__icon" viewBox="0 0 16 16" aria-hidden="true"><circle cx="8" cy="8" r="7" fill="var(--ink)"/></svg>
          @RosalindThorpeGardens
        </li>
        <li class="contact__item">
          <svg class="contact__icon" viewBox="0 0 16 16" aria-label="Website"><circle cx="8" cy="8" r="6.5" fill="none" stroke="var(--ink)" stroke-width="1.5"/><path d="M1.5 8h13M8 1.5c-3 3.5-3 9.5 0 13M8 1.5c3 3.5 3 9.5 0 13" fill="none" stroke="var(--ink)" stroke-width="1.2"/></svg>
          RosalindThorpeGardens.example
        </li>
      </ul>
    </div>
  </section>

</main>
</body>
</html>
```